Webdesign für Projektmanagement
Zielgruppe
Projektmanagement und Projektsteuerung von Bauvorhaben für Projektentwickler und Bauträger.
Wesentliche Bereiche sind Wirtschaftliche Steuerung, Steuerung der Baustelle und Bauabläufe sowie Steuerung der Marketing und Vertriebsaktivitäten.
Aufgabenstellung
Orientierung am Logo. Logo und Visitenkarte liegen bei. Schriftart Prelo und Prelo Slab.

```html
<!DOCTYPE html>
<html lang="de">
<head>
<meta charset="utf-8">
<title>Halvorn Real Estate – Start</title>
<link rel="stylesheet" href="https://fonts.googleapis.com/css2?family=Roboto+Condensed:wght@300;400;700&family=Roboto:wght@400&display=swap">
<style>
  :root{
    --navy:#0c2541;
    --navy-dark:#04182e;
    --gold:#7d703c;
    --gold-light:#c4a64e;
    --sand:#ecebe4;
    --white:#ffffff;
    --text:#2b2b2b;
  }
  *{box-sizing:border-box;margin:0;padding:0}
  html,body{width:1200px;height:1200px;overflow:hidden;background:var(--white)}
  body{font-family:"Roboto Condensed",Arial,sans-serif;color:var(--navy)}
  .page{width:1200px;height:1200px;display:flex;flex-direction:column}
  .container{width:900px;margin:0 auto;position:relative;height:100%}

  /* header */
  .site-header{height:90px;background:var(--white);flex:none}
  .brand{position:absolute;left:0;top:30px;display:flex;align-items:center;gap:8px;
    font-family:"Roboto Condensed",Arial,sans-serif;font-weight:700;font-size:27px;color:var(--navy);letter-spacing:.3px}
  .brand-mark{width:12px;height:12px;background:var(--navy)}
  .main-nav{position:absolute;right:0;top:0;height:90px;display:flex;gap:22px}
  .main-nav a{position:relative;display:block;padding:0 3px;line-height:1;padding-top:58px;
    font-size:13.5px;color:var(--navy);text-decoration:none;text-transform:uppercase}
  .main-nav a.is-active{color:var(--gold)}
  .main-nav a.is-active::after{content:"";position:absolute;left:0;right:0;bottom:0;height:3px;background:var(--gold-light)}

  /* hero */
  .hero{height:535px;flex:none;position:relative;overflow:hidden;
    background:
      linear-gradient(180deg,rgba(20,35,55,.55) 0%,rgba(20,30,45,.35) 45%,rgba(30,30,35,.55) 100%),
      linear-gradient(180deg,#2c3a4e 0%,#4a4e52 35%,#6b5a3c 62%,#3a3936 78%,#2a3340 100%);}
  .hero-title{position:absolute;left:0;right:0;top:155px;text-align:center;color:#f4f1ea;font-weight:400;text-transform:uppercase;line-height:1}
  .hero-title .line-small{display:block;font-size:57px;letter-spacing:.5px}
  .hero-title .line-large{display:block;font-size:90px;margin-top:2px;letter-spacing:1px}
  .scroll-down{position:absolute;left:577px;top:432px;width:46px;height:46px;border:1.5px solid var(--gold-light);border-radius:50%;
    display:flex;align-items:center;justify-content:center}

  /* about */
  .about{height:522px;flex:none;background:var(--sand);text-align:center}
  .about-heading{padding-top:86px;font-size:37px;font-weight:300;color:var(--navy);text-transform:uppercase;letter-spacing:.3px}
  .about-heading strong{font-weight:700}
  .services{display:flex;width:900px;margin:52px auto 0;}
  .service{width:300px;display:flex;flex-direction:column;align-items:center}
  .service-icon{height:50px;display:flex;align-items:center}
  .service-title{margin-top:34px;font-size:22px;font-weight:400;text-transform:uppercase;letter-spacing:.3px;color:var(--navy)}
  .service-text{margin-top:10px;width:285px;font-family:"Roboto",Arial,sans-serif;font-size:11px;line-height:16.5px;color:var(--text)}
  .btn{display:block;margin-top:40px;width:150px;height:33px;line-height:33px;background:var(--gold);color:var(--white);
    font-size:11px;text-transform:uppercase;text-decoration:none}

  /* footer */
  .site-footer{height:53px;flex:none;background:var(--navy-dark);color:var(--white);font-size:11px;text-transform:uppercase}
  .site-footer .container{display:flex;align-items:center;justify-content:space-between}
  .footer-nav{display:flex;gap:22px}
  .footer-nav a{color:var(--white);text-decoration:none}
</style>
</head>
<body>
<div class="page">
  <header class="site-header">
    <div class="container">
      <div class="brand"><span class="brand-mark"></span>Halvorn Real Estate</div>
      <nav class="main-nav">
        <a href="#" class="is-active">Start</a>
        <a href="#">Leistungen</a>
        <a href="#">Über uns</a>
        <a href="#">Referenzen</a>
        <a href="#">Kontakt</a>
      </nav>
    </div>
  </header>

  <section class="hero" role="img" aria-label="Abendliche Hafenszene mit geschwungenen Bürogebäuden und Booten, die sich im Wasser spiegeln">
    <h1 class="hero-title">
      <span class="line-small">Wir gestalten</span>
      <span class="line-large">Lebensraum</span>
    </h1>
    <a class="scroll-down" href="#about" aria-label="Nach unten scrollen">
      <svg width="16" height="10" viewBox="0 0 16 10"><path d="M1 1l7 7 7-7" fill="none" stroke="#c4a64e" stroke-width="1.5"/></svg>
    </a>
  </section>

  <section class="about" id="about">
    <h2 class="about-heading">Über <strong>Halvorn</strong> Real Estate</h2>
    <div class="services">
      <article class="service">
        <div class="service-icon">
          <svg width="50" height="44" viewBox="0 0 50 44" fill="none" stroke="#8a7b45" stroke-width="1.3">
            <rect x="2" y="9" width="46" height="33" rx="2"/>
            <path d="M18 9V3h14v6"/><path d="M2 23h46"/><rect x="22" y="20" width="6" height="6"/>
          </svg>
        </div>
        <h3 class="service-title">Projektmanagement</h3>
        <p class="service-text">Lorem ipsum dolor sit amet, consetetur sadipscing elitr, sed diam nonumy eirmod tempor invidunt ut labore et dolore magna aliquyam erat, sed diam voluptua.</p>
        <a class="btn" href="#">Mehr erfahren</a>
      </article>
      <article class="service">
        <div class="service-icon">
          <svg width="44" height="46" viewBox="0 0 44 46" fill="none" stroke="#8a7b45" stroke-width="1.3">
            <rect x="2" y="2" width="34" height="40"/>
            <path d="M7 10h8M19 10h12M7 17h6M17 17h10M7 24h8M19 24h6"/>
            <path d="M28 44V30a2.5 2.5 0 0 1 5 0v6h4a4 4 0 0 1 4 4v4"/>
          </svg>
        </div>
        <h3 class="service-title">Projektsteuerung</h3>
        <p class="service-text">Lorem ipsum dolor sit amet, consetetur sadipscing elitr, sed diam nonumy eirmod tempor invidunt ut labore et dolore magna aliquyam erat, sed diam voluptua.</p>
        <a class="btn" href="#">Mehr erfahren</a>
      </article>
      <article class="service">
        <div class="service-icon">
          <svg width="52" height="40" viewBox="0 0 52 40" fill="none" stroke="#8a7b45" stroke-width="1.3">
            <path d="M4 12h10l32-10v36L14 28H4z"/><path d="M46 2v36"/>
            <path d="M16 28l3 8h8l-3-7"/><path d="M4 12v16"/>
          </svg>
        </div>
        <h3 class="service-title">Marketing &amp; Vertrieb</h3>
        <p class="service-text">Lorem ipsum dolor sit amet, consetetur sadipscing elitr, sed diam nonumy eirmod tempor invidunt ut labore et dolore magna aliquyam erat, sed diam voluptua.</p>
        <a class="btn" href="#">Mehr erfahren</a>
      </article>
    </div>
  </section>

  <footer class="site-footer">
    <div class="container">
      <span>© 2017 Halvorn Real Estate GmbH</span>
      <nav class="footer-nav">
        <a href="#">Partner</a>
        <a href="#">Kontakt</a>
        <a href="#">Impressum</a>
      </nav>
    </div>
  </footer>
</div>
</body>
</html>
```